International Petrochemical business needs a web design for Clearway Desk system

We need a web design for a "Clearway Desk" system for an international petrochemical company. The web site is used internally within the company. It is hosted by an internal department which provides government permit request service for other departments.

We would like to see designs of two pages using color light blue. (home page, internal page as attached).
Home Page:
1. Header has a background image and small animation. Header on home page can be taller than the header of the internal page.
2. Layout as attached.

Internal Page:
1. Header can use the same background image as the home page and can be shorter to utilize the page for content.
2. The blue icon behind every captions represent an icon. When user move mouse over this icon, it displays the caption in Thai language as a tooltip. This icon needs to be redesign.

The final design should communicate the followings:
- Excellent service provided system in terms of time and accurary
- Rapid growth of business via building petrochemical refinery plant
Updates

For Internal Page, the blue circle behind every captions represent an icon. When mouse over this icon, a tool tip showing the caption in Thai language is shown. Please also design this icon..

There are more feedbacks from customer as followed:

1. Banner should consists of 
    1.1 "Approved" stamp on paper
    1.2 An image of Garuda. It is used on every government documents in Thailand
    1.3 Image of petrochemical plant
2. Each menu item (Home, Permit, Search, etc) should have different colors. Drop down menu will use the same color as its parent menu item.
3. Overall tone of the web page should be light blue with background of the body the web page in white
4. "New Request" button should use green color with icon on it
5. Table header of each box in the body of the page should use dark blue background with text in white

Please kindly submit your revisions.
Thank you.

Industry/Entity Type

Business

Requirements
Must have
• 1. Design for 1024x768 screen resolution
2. Use light blue theme
3. Background of header where the company logo is must have white background

```html
<!DOCTYPE html>
<html lang="en">
<head>
<meta charset="utf-8">
<title>Clearway Desk – Request Form</title>
<link href="https://fonts.googleapis.com/css2?family=Roboto:wght@400;500;700&family=Roboto+Condensed:wght@700&family=Sarabun:wght@500&display=swap" rel="stylesheet">
<style>
:root{
  --brand:#1b9ad9;
  --brand-dark:#0b74b8;
  --nav:#5bb4e3;
  --nav-dark:#3d9cd2;
  --panel:#d9f0fb;
  --panel-edge:#b9dff3;
  --field:#ffffff;
  --field-edge:#c9d6de;
  --text:#1c1c1c;
  --muted:#5d6a72;
  --chip:#c3c9cd;
  --chip-text:#707a80;
  --link:#1a6fd0;
  --tooltip:#1f1a6e;
  --footer:#3ea7dd;
}
*{box-sizing:border-box;margin:0;padding:0}
html,body{width:834px;height:1200px;overflow:hidden;background:#fff}
body{position:relative;font-family:"Roboto",Arial,sans-serif;color:var(--text)}
.abs{position:absolute}

/* header */
.brand{left:58px;top:14px;display:flex;align-items:center;gap:8px}
.brand-dot{width:26px;height:26px;border-radius:50%;background:var(--brand)}
.brand-name{font:700 15px "Roboto",Arial,sans-serif;color:var(--brand);line-height:1.05;width:110px}
.site-title{left:255px;top:26px;font:700 30px "Roboto Condensed","Roboto",sans-serif;color:var(--brand);letter-spacing:.3px}
.nav{left:0;top:65px;width:834px;height:35px;background:linear-gradient(#7cc6ec,var(--nav));border-top:1px solid #9fd6f2;border-bottom:1px solid var(--nav-dark)}
.nav a{position:absolute;top:10px;font:500 11px "Roboto",sans-serif;color:#fff;text-decoration:none;text-shadow:0 1px 1px rgba(0,0,0,.35)}
.nav .sep{position:absolute;top:10px;font-size:11px;color:#fff}
.banner{left:0;top:100px;width:834px;height:150px;background:linear-gradient(180deg,#2a3a52 0%,#7b6a66 45%,#c98a58 62%,#2b2f3c 100%)}
.fade{left:0;top:250px;width:834px;height:100px;background:linear-gradient(#8a96a2,#fff)}

/* panel */
.panel{left:48px;top:248px;width:758px;height:859px;background:var(--panel)}
.panel-title{left:48px;top:248px;width:733px;height:30px;background:linear-gradient(#49b3e6,#2a98d6);color:#fff;font:700 14px "Roboto",sans-serif;padding:7px 10px;text-shadow:0 1px 1px rgba(0,0,0,.3)}
.fold{left:781px;top:248px}
.panel-shadow{left:30px;top:1107px;width:774px;height:14px;background:radial-gradient(ellipse at top,rgba(0,0,0,.35),rgba(0,0,0,0) 70%)}

.label{font:500 11.5px "Roboto",sans-serif;text-align:right;width:160px;white-space:nowrap}
.label .req{color:#e2262b;font-size:8px;vertical-align:top;margin-left:1px}
.icon{width:28px;height:28px;background:var(--brand);border:1px solid #0f86c6;display:flex;align-items:center;justify-content:center;box-shadow:inset 0 0 0 1px #6cc6f0}
.icon svg{width:18px;height:18px}
.colon{font:700 11px "Roboto",sans-serif}
.field{height:20px;background:var(--field);border:1px solid var(--field-edge);border-radius:2px;box-shadow:inset 0 2px 2px rgba(0,0,0,.12);font:400 11px "Roboto",sans-serif;color:#444;padding:3px 8px;white-space:nowrap}
.select::after{content:"";position:absolute;right:7px;top:6px;border-left:5px solid transparent;border-right:5px solid transparent;border-top:8px solid #707070}
.area{height:71px;background:linear-gradient(#ececec,#fff 25%);border:1px solid var(--field-edge);border-radius:2px;font:400 11px "Roboto",sans-serif;color:#444;padding:6px 8px}
.btn{height:20px;border:1px solid #b5b5b5;border-radius:3px;background:linear-gradient(#fbfbfb,#dcdcdc);font:400 9.5px "Roboto",sans-serif;color:#666;display:flex;align-items:center;justify-content:center;letter-spacing:.3px}
.chip{height:13px;background:var(--chip);border:1px solid #b0b6ba;border-radius:2px;font:400 7.5px "Roboto",sans-serif;color:var(--chip-text);padding:1px 5px;white-space:nowrap}
.chip b{position:absolute;right:0;top:-1px;width:18px;height:13px;background:#eee;border:1px solid #aaa;font:500 8px "Roboto",sans-serif;color:#555;text-align:center;line-height:11px}

.tooltip{left:494px;top:362px;width:132px;height:37px;background:var(--tooltip);border-radius:3px;color:#fff;font:500 8.5px "Sarabun","Roboto",sans-serif;padding:5px 9px;line-height:12px}
.tooltip::before{content:"";position:absolute;left:117px;top:-6px;border-left:6px solid transparent;border-right:6px solid transparent;border-bottom:6px solid var(--tooltip)}

.related{left:228px;top:929px;width:320px;height:123px;background:#fff;border-radius:3px}
.related-head{left:0;top:0;width:320px;height:28px;background:linear-gradient(#e4e4e4,#fff);border-radius:3px 3px 0 0}
.related .th{position:absolute;top:8px;font:500 10.5px "Roboto",sans-serif;color:#555}
.related .td{position:absolute;font:400 9px "Roboto",sans-serif;color:#333}
.related .td.link{color:var(--link);text-decoration:underline}
.related .col-line{position:absolute;top:28px;width:1px;height:72px;background:#d6d6d6}
.pager{left:346px;top:1037px;width:100px;height:16px;background:var(--brand);font:500 7.5px "Roboto",sans-serif;color:#fff;display:flex;align-items:center;justify-content:space-around;padding:0 6px}

.action{height:28px;border:1px solid #a9a9a9;border-radius:3px;background:linear-gradient(#fafafa,#d4d4d4);font:500 12px "Roboto",sans-serif;color:#777;display:flex;align-items:center;justify-content:center;box-shadow:0 1px 2px rgba(0,0,0,.25)}

.footer{left:0;top:1124px;width:834px;height:76px;background:linear-gradient(#5db9e8,var(--footer) 50%,#8fd0f0)}
.footer-line{left:0;top:1121px;width:834px;height:3px;background:#2d7fb4}
.footer .copy,.footer .legal{position:absolute;top:17px;font:400 7.5px "Roboto",sans-serif;color:#123}
</style>
</head>
<body>

<!-- header -->
<div class="abs brand"><span class="brand-dot"></span><span class="brand-name">Northbay Refining</span></div>
<div class="abs site-title">CLEARWAY DESK</div>

<nav class="abs nav">
  <a style="left:75px">HOME</a><span class="sep" style="left:134px">|</span>
  <a style="left:162px">PERMITS</a><span class="sep" style="left:222px">|</span>
  <a style="left:249px">SEARCH</a><span class="sep" style="left:309px">|</span>
  <a style="left:339px">REPORT</a><span class="sep" style="left:397px">|</span>
  <a style="left:426px">ADMIN</a><span class="sep" style="left:484px">|</span>
  <a style="left:510px">HELP</a>
</nav>
<div class="abs banner" role="img" aria-label="Petrochemical refinery plant lit at dusk beside a river"></div>
<div class="abs fade"></div>

<!-- form panel -->
<div class="abs panel"></div>
<div class="abs panel-title">Request Form</div>
<svg class="abs fold" width="25" height="30" viewBox="0 0 25 30"><path d="M0 0 L25 22 L25 30 L0 30Z" fill="#9fd2ee"/><path d="M0 0 L25 22 L0 22Z" fill="#cfe9f7"/></svg>

<!-- left column rows -->
<div class="abs label" style="left:17px;top:301px">Request Date</div>
<div class="abs icon" style="left:183px;top:294px"><svg viewBox="0 0 18 18"><rect x="2" y="4" width="14" height="12" fill="none" stroke="#fff" stroke-width="1.6"/><path d="M2 7h14M6 2v4M12 2v4" stroke="#fff" stroke-width="1.6"/></svg></div>
<div class="abs colon" style="left:219px;top:300px">:</div>
<div class="abs field" style="left:230px;top:298px;width:35px">21</div>
<div class="abs field select" style="left:272px;top:298px;width:73px">January</div>
<div class="abs field" style="left:352px;top:298px;width:45px">2013</div>

<div class="abs label" style="left:17px;top:336px">Requester Name</div>
<div class="abs icon" style="left:183px;top:329px"><svg viewBox="0 0 18 18"><rect x="2" y="3" width="14" height="11" rx="1" fill="none" stroke="#fff" stroke-width="1.6"/><circle cx="7" cy="8" r="2" fill="#fff"/><path d="M10 7h4M10 10h4" stroke="#fff" stroke-width="1.4"/></svg></div>
<div class="abs colon" style="left:219px;top:335px">:</div>
<div class="abs field" style="left:230px;top:333px;width:205px">Alan Reed</div>

<div class="abs label" style="left:17px;top:372px">Contact No</div>
<div class="abs icon" style="left:183px;top:365px"><svg viewBox="0 0 18 18"><rect x="5" y="2" width="8" height="14" rx="1.5" fill="none" stroke="#fff" stroke-width="1.6"/><path d="M7 13h4" stroke="#fff" stroke-width="1.4"/></svg></div>
<div class="abs colon" style="left:219px;top:371px">:</div>
<div class="abs field" style="left:230px;top:369px;width:205px">0900 5521 7384</div>

<div class="abs label" style="left:17px;top:407px">Company<span class="req">*</span></div>
<div class="abs icon" style="left:183px;top:400px"><svg viewBox="0 0 18 18"><rect x="2" y="4" width="14" height="11" fill="none" stroke="#fff" stroke-width="1.6"/><path d="M6 6v7M9 6v7M12 6v7" stroke="#fff" stroke-width="1.4"/></svg></div>
<div class="abs colon" style="left:219px;top:406px">:</div>
<div class="abs field select" style="left:230px;top:404px;width:205px">Please select</div>

<div class="abs label" style="left:17px;top:443px">Branch<span class="req">*</span></div>
<div class="abs icon" style="left:183px;top:436px"><svg viewBox="0 0 18 18"><rect x="7" y="2" width="4" height="4" fill="#fff"/><rect x="2" y="12" width="4" height="4" fill="#fff"/><rect x="12" y="12" width="4" height="4" fill="#fff"/><path d="M9 6v3M4 12V9h10v3" fill="none" stroke="#fff" stroke-width="1.4"/></svg></div>
<div class="abs colon" style="left:219px;top:442px">:</div>
<div class="abs field select" style="left:230px;top:440px;width:205px">Please select</div>

<div class="abs label" style="left:17px;top:478px">Document Category<span class="req">*</span></div>
<div class="abs icon" style="left:183px;top:471px"><svg viewBox="0 0 18 18"><path d="M4 2h7l3 3v11H4Z" fill="none" stroke="#fff" stroke-width="1.5"/><path d="M6 10l2 2 4-4" fill="none" stroke="#fff" stroke-width="1.5"/></svg></div>
<div class="abs colon" style="left:219px;top:477px">:</div>
<div class="abs field select" style="left:230px;top:475px;width:205px">Please select</div>

<div class="abs label" style="left:17px;top:514px">Document Type<span class="req">*</span></div>
<div class="abs icon" style="left:183px;top:507px"><svg viewBox="0 0 18 18"><path d="M4 2h7l3 3v11H4Z" fill="none" stroke="#fff" stroke-width="1.5"/><rect x="3" y="10" width="8" height="4" fill="#fff"/></svg></div>
<div class="abs colon" style="left:219px;top:513px">:</div>
<div class="abs field select" style="left:230px;top:511px;width:205px">Please select</div>

<div class="abs label" style="left:17px;top:549px">Expected Use Date<span class="req">*</span></div>
<div class="abs icon" style="left:183px;top:542px"><svg viewBox="0 0 18 18"><rect x="2" y="4" width="14" height="12" fill="none" stroke="#fff" stroke-width="1.6"/><path d="M2 7h14" stroke="#fff" stroke-width="1.6"/><path d="M8 10l2-1v6" fill="none" stroke="#fff" stroke-width="1.6"/></svg></div>
<div class="abs colon" style="left:219px;top:548px">:</div>
<div class="abs field" style="left:230px;top:546px;width:35px">28</div>
<div class="abs field select" style="left:272px;top:546px;width:73px">January</div>
<div class="abs field" style="left:352px;top:546px;width:45px">2013</div>

<div class="abs label" style="left:17px;top:585px">Detail<span class="req">*</span></div>
<div class="abs icon" style="left:183px;top:578px"><svg viewBox="0 0 18 18"><rect x="2" y="3" width="11" height="13" fill="none" stroke="#fff" stroke-width="1.5"/><path d="M8 12l8-8" stroke="#fff" stroke-width="2"/></svg></div>
<div class="abs colon" style="left:219px;top:584px">:</div>
<div class="abs area" style="left:230px;top:579px;width:205px">Lorem ipsum dolor sit amet</div>

<div class="abs label" style="left:17px;top:673px">Attachment</div>
<div class="abs icon" style="left:183px;top:666px"><svg viewBox="0 0 18 18"><path d="M12 5l-6 6a2 2 0 0 0 3 3l6-6a3.5 3.5 0 0 0-5-5l-6 6" fill="none" stroke="#fff" stroke-width="1.5"/></svg></div>
<div class="abs colon" style="left:219px;top:672px">:</div>
<div class="abs field" style="left:230px;top:671px;width:205px">confidential.doc</div>
<div class="abs btn" style="left:442px;top:671px;width:59px">BROWSE</div>
<div class="abs btn" style="left:509px;top:671px;width:58px">ATTACH</div>
<div class="abs chip" style="left:230px;top:695px;width:62px">file1.doc<b>X</b></div>
<div class="abs chip" style="left:297px;top:695px;width:62px">file1.doc<b>X</b></div>
<div class="abs chip" style="left:366px;top:695px;width:62px">file1.doc<b>X</b></div>

<div class="abs label" style="left:17px;top:726px">Coordinator<span class="req">*</span></div>
<div class="abs icon" style="left:183px;top:719px"><svg viewBox="0 0 18 18"><circle cx="9" cy="6" r="3.2" fill="#fff"/><path d="M3 16c0-4 3-6 6-6s6 2 6 6Z" fill="#fff"/></svg></div>
<div class="abs colon" style="left:219px;top:725px">:</div>
<div class="abs btn" style="left:230px;top:724px;width:58px">ADD</div>
<div class="abs chip" style="left:230px;top:748px;width:90px">Alan Reed HR<b>X</b></div>

<div class="abs label" style="left:17px;top:780px">Related Person<span class="req">*</span></div>
<div class="abs icon" style="left:183px;top:773px"><svg viewBox="0 0 18 18"><circle cx="6" cy="7" r="2.5" fill="#fff"/><circle cx="12" cy="7" r="2.5" fill="#fff"/><path d="M1 15c0-3 2-5 5-5s5 2 5 5ZM8 15c0-3 2-5 4-5s5 2 5 5Z" fill="#fff"/></svg></div>
<div class="abs colon" style="left:219px;top:779px">:</div>
<div class="abs btn" style="left:230px;top:776px;width:58px">ADD</div>
<div class="abs chip" style="left:230px;top:799px;width:90px">Nina Holt (IT)<b>X</b></div>
<div class="abs chip" style="left:323px;top:799px;width:107px">Paul Vance (Finance)<b>X</b></div>
<div class="abs chip" style="left:230px;top:816px;width:113px">Omar Lind (Finance)<b>X</b></div>

<div class="abs label" style="left:17px;top:851px">Remark</div>
<div class="abs icon" style="left:183px;top:844px"><svg viewBox="0 0 18 18"><rect x="2" y="3" width="14" height="10" rx="1" fill="none" stroke="#fff" stroke-width="1.5"/><path d="M5 16l2-3" stroke="#fff" stroke-width="1.5"/><path d="M5 8h1M8 8h1M11 8h1" stroke="#fff" stroke-width="1.8"/></svg></div>
<div class="abs colon" style="left:219px;top:850px">:</div>
<div class="abs area" style="left:230px;top:842px;width:205px">Lorem ipsum dolor sit amet</div>

<div class="abs label" style="left:17px;top:939px">Related Request</div>
<div class="abs icon" style="left:183px;top:932px"><svg viewBox="0 0 18 18"><ellipse cx="9" cy="8" rx="7" ry="5" fill="#fff"/><path d="M4 16l2-4 3 1Z" fill="#fff"/></svg></div>
<div class="abs colon" style="left:219px;top:938px">:</div>

<div class="abs related">
  <div class="abs related-head"></div>
  <span class="th" style="left:11px">Request No.</span>
  <span class="th" style="left:98px">Request Date</span>
  <span class="th" style="left:185px">Company</span>
  <span class="th" style="left:254px">Branch</span>
  <span class="col-line" style="left:84px"></span>
  <span class="col-line" style="left:177px"></span>
  <span class="col-line" style="left:246px"></span>
  <span class="td link" style="left:11px;top:38px">AB56001</span><span class="td" style="left:98px;top:38px">20/4/2013</span><span class="td" style="left:185px;top:38px">NBR</span><span class="td" style="left:254px;top:38px">GC1</span>
  <span class="td link" style="left:11px;top:53px">BIO5502</span><span class="td" style="left:98px;top:53px">21/4/2013</span><span class="td" style="left:185px;top:53px">NBR</span><span class="td" style="left:254px;top:53px">GC2</span>
  <span class="td link" style="left:11px;top:67px">AB56001</span><span class="td" style="left:98px;top:67px">20/4/2013</span><span class="td" style="left:185px;top:67px">XYZ</span><span class="td" style="left:254px;top:67px">GC3</span>
  <span class="td link" style="left:11px;top:82px">BIO5502</span><span class="td" style="left:98px;top:82px">21/4/2013</span><span class="td" style="left:185px;top:82px">XYZ</span><span class="td" style="left:254px;top:82px">GC4</span>
</div>
<div class="abs pager"><span>&#8249;</span><span>1</span><span>2</span><span>3</span><span>4</span><span>5</span><span>&#8250;</span></div>

<div class="abs action" style="left:228px;top:1062px;width:90px;justify-content:flex-start">
  <svg width="28" height="26" viewBox="0 0 28 26" style="border-right:1px solid #bbb"><path d="M16 8l-5 5 5 5" fill="none" stroke="#666" stroke-width="2.2"/></svg>
  <span style="margin-left:9px">BACK</span>
</div>
<div class="abs action" style="left:326px;top:1062px;width:222px">CREATE NEW REQUEST</div>

<!-- right column -->
<div class="abs label" style="left:417px;top:301px">Requester Employee No</div>
<div class="abs icon" style="left:583px;top:294px"><svg viewBox="0 0 18 18"><circle cx="9" cy="9" r="7" fill="none" stroke="#fff" stroke-width="1.5"/><text x="9" y="12" text-anchor="middle" font-size="8" font-family="Roboto,sans-serif" font-weight="700" fill="#fff">10</text></svg></div>
<div class="abs colon" style="left:619px;top:300px">:</div>
<div class="abs field" style="left:630px;top:298px;width:148px">5510 20874 3361</div>

<div class="abs label" style="left:417px;top:336px">Telephone</div>
<div class="abs icon" style="left:583px;top:329px"><svg viewBox="0 0 18 18"><path d="M4 3l3 0 1 3-2 1.5a9 9 0 0 0 4.5 4.5L12 10l3 1v3c-6 1-12-5-11-11Z" fill="#fff"/></svg></div>
<div class="abs colon" style="left:619px;top:335px">:</div>
<div class="abs field" style="left:630px;top:333px;width:148px">3108 7720 914</div>

<div class="abs tooltip" lang="th">ระหว่างดำเนินการรอดำเนินก<br>ารรอดำเนินการ</div>

<!-- footer -->
<div class="abs panel-shadow"></div>
<div class="abs footer-line"></div>
<footer class="abs footer" role="img" aria-label="Faint blue refinery plant backdrop">
  <span class="copy" style="left:58px">Copyright © 2013 NorthbayRefining. All rights reserved.</span>
  <span class="legal" style="left:686px">Terms and Condition | Privacy</span>
</footer>

</body>
</html>
```